Business Card Design

New business card design

Target Market(s)

Residential & Commercial Property Managers

Industry/Entity Type

Plumbing Services

Contact Information for Business Card

Name - Rowan Keddle, title - Director, Phone Number - 0431 286 517, email - rowan@tbk-plumbing.com.au, Company ABN - 73 215 904 386,

Font styles to use
Sans Serif

Colors
0054AA
0677BA
7BADD7
CADEEF
E8F1F8

```html
<!DOCTYPE html>
<html lang="en">
<head>
<meta charset="utf-8">
<title>TBK Plumbing Services – Business Card</title>
<link href="https://fonts.googleapis.com/css2?family=Montserrat:wght@400;500;700&display=swap" rel="stylesheet">
<style>
  :root {
    --backdrop: #161718;
    --card-light: #f4f4f4;
    --card-dark: #1c232a;
    --accent-blue: #2aa4dc;
    --ink: #1d1f22;
    --white: #ffffff;
  }
  * { margin: 0; padding: 0; box-sizing: border-box; }
  html, body {
    width: 1200px;
    height: 1059px;
    overflow: hidden;
    background: var(--backdrop);
    font-family: "Montserrat", sans-serif;
  }
  .canvas {
    position: relative;
    width: 1200px;
    height: 1059px;
  }
  .card {
    position: absolute;
    width: 690px;
    height: 390px;
    border-radius: 24px;
    overflow: hidden;
  }
  .card-front {
    left: 255px;
    top: 89px;
    background: var(--card-light);
  }
  .card-back {
    left: 255px;
    top: 547px;
    background: var(--card-dark);
  }
  .front-wave {
    position: absolute;
    left: 0;
    top: 0;
    width: 690px;
    height: 390px;
  }
  .brand {
    position: absolute;
    display: flex;
    align-items: center;
    gap: 10px;
    white-space: nowrap;
  }
  .brand-dot {
    border-radius: 50%;
    background: var(--accent-blue);
    flex: none;
  }
  .card-front .brand {
    left: 0;
    width: 343px;
    top: 168px;
    justify-content: center;
    font-size: 22px;
    font-weight: 500;
    color: var(--card-dark);
  }
  .card-front .brand-dot { width: 14px; height: 14px; }
  .divider {
    position: absolute;
    left: 343px;
    top: 121px;
    width: 1.5px;
    height: 150px;
    background: var(--accent-blue);
  }
  .contact {
    position: absolute;
    left: 372px;
    top: 116px;
    color: var(--ink);
  }
  .contact-name {
    font-size: 26px;
    font-weight: 700;
    color: var(--accent-blue);
    line-height: 1;
  }
  .contact-title {
    font-size: 17px;
    margin-top: 4px;
    line-height: 1;
  }
  .contact-abn {
    font-size: 18px;
    margin-top: 22px;
    line-height: 1;
  }
  .contact-abn .label { color: var(--accent-blue); }
  .contact-line {
    display: flex;
    align-items: center;
    gap: 8px;
    font-size: 18px;
    line-height: 1;
  }
  .contact-line.phone { margin-top: 24px; }
  .contact-line.email { margin-top: 10px; }
  .contact-line svg { width: 12px; height: 12px; flex: none; }
  .card-back .brand {
    left: 0;
    right: 0;
    top: 168px;
    justify-content: center;
    font-size: 40px;
    font-weight: 500;
    color: var(--white);
    gap: 16px;
  }
  .card-back .brand-dot { width: 24px; height: 24px; }
</style>
</head>
<body>
<main class="canvas">

  <section class="card card-front" aria-label="Business card front">
    <svg class="front-wave" viewBox="0 0 690 390" aria-hidden="true">
      <path d="M0 322 Q345 392 690 322 L690 390 L0 390 Z" fill="var(--card-dark)"/>
      <path d="M30 325 Q345 388 660 325 Q345 380 30 325 Z" fill="var(--accent-blue)"/>
    </svg>

    <div class="brand">
      <span class="brand-dot"></span>
      <span class="brand-name">TBK Plumbing Services</span>
    </div>

    <div class="divider"></div>

    <div class="contact">
      <p class="contact-name">Rowan Keddle</p>
      <p class="contact-title">Director</p>
      <p class="contact-abn"><span class="label">ABN</span> - 73 215 904 386</p>
      <p class="contact-line phone">
        <svg viewBox="0 0 24 24" aria-hidden="true"><path fill="var(--accent-blue)" d="M6.6 10.8a15.1 15.1 0 0 0 6.6 6.6l2.2-2.2c.3-.3.7-.4 1-.2 1.1.4 2.3.6 3.6.6.6 0 1 .4 1 1V20c0 .6-.4 1-1 1A17 17 0 0 1 3 4c0-.6.4-1 1-1h3.5c.6 0 1 .4 1 1 0 1.3.2 2.5.6 3.6.1.3 0 .7-.2 1l-2.3 2.2z"/></svg>
        <span>0431 286 517</span>
      </p>
      <p class="contact-line email">
        <svg viewBox="0 0 24 24" aria-hidden="true"><path fill="var(--accent-blue)" d="M2 5h20v14H2z"/><path d="M2 5l10 8 10-8M2 19l8-7M22 19l-8-7" stroke="var(--card-light)" stroke-width="1.6" fill="none"/></svg>
        <span>rowan@tbk-plumbing.com.au</span>
      </p>
    </div>
  </section>

  <section class="card card-back" aria-label="Business card back">
    <div class="brand">
      <span class="brand-dot"></span>
      <span class="brand-name">TBK Plumbing Services</span>
    </div>
  </section>

</main>
</body>
</html>
```